Maple Rug & Vent Cleaning

redesign of current website www.birchfreshrugwashing.net Looking for something similar to what we have but more professional and more user-friendly modern design for homepage and service page. A more professional looking contact form in the slider area of the homepage and a way to display 5 different phone number and regions above the fold, preferably the header.

Target Market(s)

Homeowners looking for top tier all-natural organic cleaning for their carpets, area rugs and air ducts.

Industry/Entity Type

Carpet

Number of Pages Required

2 page

Font styles to use
Sans Serif

Colors

Designer to choose colors to be used in the design.

Requirements
Must have
• A more professional looking contact form in the slider area of the homepage and a clear call to action
Nice to have
• a way to display 5 different phone numbers and regions above the fold, preferably the header.

```html
<!DOCTYPE html>
<html lang="en">
<head>
<meta charset="utf-8">
<title>Maple Rug &amp; Vent Cleaning</title>
<link href="https://fonts.googleapis.com/css2?family=Montserrat:wght@500;600;700;800&family=Open+Sans:wght@400;600;700&display=swap" rel="stylesheet">
<style>
:root{
  --blue:#1565c0;
  --blue-dark:#0d3f8f;
  --green:#2e9d3a;
  --green-dark:#1f7a2a;
  --navy:#0b2540;
  --navy-deep:#081a2e;
  --gray-bg:#eef0f2;
  --text:#2b2f36;
  --muted:#6b7280;
  --white:#ffffff;
}
*{margin:0;padding:0;box-sizing:border-box}
html,body{width:1200px;height:3472px;overflow:hidden}
body{font-family:"Open Sans",Arial,sans-serif;color:var(--text);background:var(--white);position:relative}
h1,h2,h3,.nav,.btn{font-family:"Montserrat",Arial,sans-serif}

.topbar{position:absolute;top:0;left:0;width:1200px;height:40px;background:var(--blue);display:flex;justify-content:center;align-items:center;gap:26px;color:var(--white);font-size:12px;font-weight:600}
.topbar span{display:flex;align-items:center;gap:6px}
.topbar svg{width:12px;height:12px;fill:var(--white)}

.header{position:absolute;top:40px;left:0;width:1200px;height:76px;background:var(--white);display:flex;align-items:center;padding:0 50px;z-index:3;box-shadow:0 2px 6px rgba(0,0,0,.08)}
.brand{display:flex;align-items:center;gap:10px;font-family:"Montserrat",sans-serif;font-weight:800;font-size:22px;color:var(--green);line-height:1}
.brand i{display:block;width:22px;height:22px;border-radius:50%;background:var(--green)}
.nav{margin-left:auto;display:flex;gap:30px;font-size:13px;font-weight:700;color:var(--text)}
.nav a.active{color:var(--green)}

.hero{position:absolute;top:116px;left:0;width:1200px;height:580px;background:linear-gradient(110deg,#f4f6f7 0%,#e6ecef 40%,#c9d6de 70%,#b8c7d0 100%)}
.hero-copy{position:absolute;top:220px;left:210px}
.hero-copy h1{font-size:42px;font-weight:800;color:var(--green);line-height:1.05}
.hero-copy h1 small{display:block;font-size:30px;color:var(--blue);font-weight:700;margin-top:4px}
.btn{display:inline-block;background:var(--blue);color:var(--white);font-weight:700;font-size:15px;padding:14px 26px;border-radius:3px;margin-top:26px}
.form{position:absolute;top:180px;left:780px;width:320px;height:470px;background:var(--green);padding:20px 22px;color:var(--white);z-index:2}
.form h3{font-size:18px;font-weight:700;margin-bottom:14px}
.field{height:34px;background:var(--white);border-radius:2px;margin-bottom:10px;color:#8a8f96;font-size:12px;padding:9px 10px}
.checks{background:var(--white);border-radius:2px;padding:12px 10px;display:grid;grid-template-columns:1fr 1fr;gap:8px 6px;margin-bottom:10px;font-size:11px;color:var(--text)}
.checks span{display:flex;align-items:center;gap:5px}
.checks span::before{content:"";width:10px;height:10px;border:1px solid #999;flex:none}
.field.msg{height:70px}
.submit{height:44px;background:var(--blue);border-radius:2px;display:flex;align-items:center;justify-content:center;font-family:"Montserrat",sans-serif;font-weight:700;font-size:15px}
.hero-wave{position:absolute;top:640px;left:0;width:1200px;height:90px}

.why{position:absolute;top:860px;left:0;width:1200px;text-align:center}
.why h2{font-size:24px;font-weight:700;color:var(--navy);line-height:1.35}
.features{position:absolute;top:1005px;left:160px;width:900px;display:grid;grid-template-columns:repeat(3,1fr);row-gap:100px}
.feature{display:flex;align-items:center;gap:14px;font-size:15px;line-height:1.3}
.feature svg{width:40px;height:40px;flex:none;stroke:var(--green);fill:none;stroke-width:2}

.services{position:absolute;top:1300px;left:0;width:1200px;height:470px;background:var(--gray-bg)}
.services h2,.projects h2,.testimonials h2{text-align:center;font-size:30px;font-weight:700}
.services h2{color:var(--blue);margin-top:70px}
.circle{position:absolute;top:150px;width:300px;height:300px;border-radius:50%;border:6px solid var(--green);overflow:hidden;display:flex;flex-direction:column;align-items:center;justify-content:flex-end;padding-bottom:50px;color:var(--white);font-family:"Montserrat",sans-serif;font-weight:700;font-size:17px;text-align:center}
.c1{left:145px;background:linear-gradient(160deg,#d8d5cf,#8f8b84)}
.c2{left:450px;background:var(--green);justify-content:center;padding:0 40px}
.c2 p{font-family:"Open Sans",sans-serif;font-weight:400;font-size:12px;margin:10px 0 14px}
.c2 .more{background:var(--white);color:var(--green);font-size:12px;padding:7px 16px;border-radius:2px}
.c3{left:755px;background:linear-gradient(160deg,#c9cbcc,#6f7375)}
.arrow{position:absolute;top:290px;width:20px;height:20px;stroke:#666;fill:none;stroke-width:3}

.projects{position:absolute;top:1800px;left:0;width:1200px;height:600px;background:var(--blue)}
.projects h2{color:var(--white);margin-top:50px}
.grid{position:absolute;top:112px;left:152px;width:896px;display:grid;grid-template-columns:repeat(3,1fr);grid-template-rows:216px 216px;gap:10px}
.tile{border-radius:2px}
.t1{background:linear-gradient(150deg,#cfd2d6,#7c8088)}
.t2{background:linear-gradient(150deg,#3a3f46,#1c1f24);display:flex;align-items:center;justify-content:center;color:var(--white);text-align:center;font-size:14px;line-height:1.4;padding:30px}
.t3{background:linear-gradient(150deg,#b59a7c,#6b5440)}
.t4{background:linear-gradient(150deg,#8a7a66,#4b4036)}
.t5{background:linear-gradient(150deg,#3b3e42,#16181b)}
.t6{background:linear-gradient(150deg,#d9d2c8,#8c7f70)}

.testimonials{position:absolute;top:2420px;left:0;width:1200px;height:430px}
.testimonials h2{color:var(--navy);margin-top:50px}
.card{position:absolute;top:140px;width:410px;height:230px;border:1px solid #d9dde2;padding:26px 28px;font-size:13px;line-height:1.6;color:var(--muted)}
.card .stars{color:#f5a623;font-size:20px;letter-spacing:2px;line-height:1}
.card h3{font-size:18px;color:var(--text);margin:8px 0 10px}
.card .author{margin-top:12px;color:var(--text)}

.badges{position:absolute;top:2880px;left:170px;width:860px;display:flex;justify-content:space-between;align-items:center}
.badge{background:#cfd6dd}
.b-round{width:80px;height:80px;border-radius:50%}
.b-rect{width:100px;height:64px;border-radius:4px}
.b-sq{width:76px;height:76px;border-radius:6px}

.footer-wave{position:absolute;top:2990px;left:0;width:1200px;height:70px}
.footer{position:absolute;top:3040px;left:0;width:1200px;height:432px;background:var(--navy);color:#c8d2dd}
.footer h3{color:var(--white);font-size:16px;font-weight:700;margin-bottom:18px}
.fcol{position:absolute;top:50px;font-size:13px;line-height:1.9}
.links{display:grid;grid-template-columns:130px 130px}
.social{display:flex;gap:10px;margin-top:16px}
.social i{width:30px;height:30px;border-radius:50%;border:2px solid #c8d2dd;display:block}
.copy{position:absolute;bottom:0;left:0;width:1200px;height:70px;background:var(--navy-deep);display:flex;align-items:center;justify-content:center;font-size:12px}
</style>
</head>
<body>

<div class="topbar">
  <span><svg viewBox="0 0 24 24"><path d="M6.6 10.8a15 15 0 0 0 6.6 6.6l2.2-2.2a1 1 0 0 1 1-.25 11.4 11.4 0 0 0 3.6.57 1 1 0 0 1 1 1V20a1 1 0 0 1-1 1A17 17 0 0 1 3 4a1 1 0 0 1 1-1h3.5a1 1 0 0 1 1 1c0 1.25.2 2.45.57 3.57a1 1 0 0 1-.25 1z"/></svg>CHICAGO (773) 555-0142</span>
  <span><svg viewBox="0 0 24 24"><path d="M6.6 10.8a15 15 0 0 0 6.6 6.6l2.2-2.2a1 1 0 0 1 1-.25 11.4 11.4 0 0 0 3.6.57 1 1 0 0 1 1 1V20a1 1 0 0 1-1 1A17 17 0 0 1 3 4a1 1 0 0 1 1-1h3.5a1 1 0 0 1 1 1c0 1.25.2 2.45.57 3.57a1 1 0 0 1-.25 1z"/></svg>NORTH &amp; NW SUBURBS (847) 555-0187</span>
  <span><svg viewBox="0 0 24 24"><path d="M6.6 10.8a15 15 0 0 0 6.6 6.6l2.2-2.2a1 1 0 0 1 1-.25 11.4 11.4 0 0 0 3.6.57 1 1 0 0 1 1 1V20a1 1 0 0 1-1 1A17 17 0 0 1 3 4a1 1 0 0 1 1-1h3.5a1 1 0 0 1 1 1c0 1.25.2 2.45.57 3.57a1 1 0 0 1-.25 1z"/></svg>SOUTHWEST SUBURBS (630) 555-0123</span>
  <span><svg viewBox="0 0 24 24"><path d="M6.6 10.8a15 15 0 0 0 6.6 6.6l2.2-2.2a1 1 0 0 1 1-.25 11.4 11.4 0 0 0 3.6.57 1 1 0 0 1 1 1V20a1 1 0 0 1-1 1A17 17 0 0 1 3 4a1 1 0 0 1 1-1h3.5a1 1 0 0 1 1 1c0 1.25.2 2.45.57 3.57a1 1 0 0 1-.25 1z"/></svg>NEAR WEST SUBURBS (708) 555-0166</span>
  <span><svg viewBox="0 0 24 24"><path d="M6.6 10.8a15 15 0 0 0 6.6 6.6l2.2-2.2a1 1 0 0 1 1-.25 11.4 11.4 0 0 0 3.6.57 1 1 0 0 1 1 1V20a1 1 0 0 1-1 1A17 17 0 0 1 3 4a1 1 0 0 1 1-1h3.5a1 1 0 0 1 1 1c0 1.25.2 2.45.57 3.57a1 1 0 0 1-.25 1z"/></svg>SOUTH SUBURBS (815) 555-0194</span>
</div>

<header class="header">
  <div class="brand"><i></i>MAPLE RUG &amp; VENT</div>
  <nav class="nav">
    <a class="active">HOME</a><a>WHY MAPLE RUG</a><a>OUR SERVICES</a><a>COUPONS</a><a>GALLERY</a><a>SERVICE AREA</a><a>CONTACT</a>
  </nav>
</header>

<section class="hero" role="img" aria-label="Photo of a smiling woman in yellow gloves scrubbing a light carpet beside a red cleaning bucket">
</section>
<div class="hero-copy">
  <h1>ORGANIC CARPET<small>CLEANING SERVICES</small></h1>
  <a class="btn">Get Free Estimate</a>
</div>
<form class="form">
  <h3>CONTACT FORM</h3>
  <div class="field">Name</div>
  <div class="field">Email address</div>
  <div class="field">Phone number</div>
  <div class="checks">
    <span>Air Duct Cleaning</span><span>Carpet Cleaning</span>
    <span>Area Rug Cleaning</span><span>Pet Odor Removal</span>
    <span>Water Damage Restoration</span>
  </div>
  <div class="field msg">Message or Preferred Date &amp; Time</div>
  <div class="submit">Submit Now</div>
</form>
<svg class="hero-wave" viewBox="0 0 1200 90" preserveAspectRatio="none">
  <path d="M0 40 Q600 110 1200 20 V90 H0Z" fill="#1565c0"/>
  <path d="M0 50 Q600 115 1200 32 V90 H0Z" fill="#2e9d3a"/>
  <path d="M0 62 Q600 120 1200 46 V90 H0Z" fill="#ffffff"/>
</svg>

<section class="why">
  <h2>WHY USE MAPLE RUG &amp; VENT FOR ALL YOUR CARPET<br>&amp; AIR DUCT CLEANING NEEDS?</h2>
</section>
<div class="features">
  <div class="feature"><svg viewBox="0 0 40 40"><path d="M8 32 C8 14 20 8 34 8 C34 22 26 32 8 32Z M8 32 L24 18"/></svg>We Proudly Use Only<br>Certified Green Products</div>
  <div class="feature"><svg viewBox="0 0 40 40"><path d="M20 4 L34 9 V20 C34 28 28 34 20 37 C12 34 6 28 6 20 V9Z M13 20 L18 25 L27 15"/></svg>Industry Leading One Year<br>Guarantee on Services</div>
  <div class="feature"><svg viewBox="0 0 40 40"><circle cx="20" cy="16" r="10"/><path d="M14 24 L11 36 L20 31 L29 36 L26 24"/></svg>Over 20 years of Green<br>Cleaning Experience</div>
  <div class="feature"><svg viewBox="0 0 40 40"><path d="M20 4 L23 16 L35 20 L23 24 L20 36 L17 24 L5 20 L17 16Z"/></svg>Most Powerful Cleaning<br>Technology on the Market</div>
  <div class="feature"><svg viewBox="0 0 40 40"><path d="M14 6 H26 M16 6 V14 L8 32 C7 35 9 36 11 36 H29 C31 36 33 35 32 32 L24 14 V6"/></svg>Non-toxic Biodegradable<br>Detergents</div>
  <div class="feature"><svg viewBox="0 0 40 40"><rect x="6" y="6" width="28" height="24" rx="2"/><path d="M13 18 L18 23 L27 13 M14 36 H26"/></svg>Certified, Trained &amp; Well<br>Screened Technicians</div>
</div>

<section class="services">
  <h2>OUR SERVICES</h2>
  <svg class="arrow" style="left:95px" viewBox="0 0 20 20"><path d="M14 2 L6 10 L14 18"/></svg>
  <div class="circle c1" role="img" aria-label="Photo of a vacuum head cleaning carpet">CARPET<br>CLEANING</div>
  <div class="circle c2">UPHOLSTERY<br>CLEANING<p>Gentle deep cleaning that lifts stains and refreshes fabric.</p><span class="more">Learn More</span></div>
  <div class="circle c3" role="img" aria-label="Photo of a metal air vent grille">AIR DUCT<br>CLEANING</div>
  <svg class="arrow" style="left:1085px" viewBox="0 0 20 20"><path d="M6 2 L14 10 L6 18"/></svg>
</section>

<section class="projects">
  <h2>RECENT PROJECTS</h2>
  <div class="grid">
    <div class="tile t1" role="img" aria-label="Photo of a cleaned tufted upholstered headboard"></div>
    <div class="tile t2">2 hrs, Deodorized, Steam<br>cleaned, Pretreated,<br>Sanitized and fabric protected</div>
    <div class="tile t3" role="img" aria-label="Photo of freshly cleaned carpeted stairs"></div>
    <div class="tile t4" role="img" aria-label="Photo of a living room rug under a coffee table"></div>
    <div class="tile t5" role="img" aria-label="Photo of a cleaned dark leather sofa"></div>
    <div class="tile t6" role="img" aria-label="Photo of a bright carpeted room after cleaning"></div>
  </div>
</section>

<section class="testimonials">
  <h2>TESTIMONIALS</h2>
  <svg class="arrow" style="left:140px;top:240px" viewBox="0 0 20 20"><path d="M14 2 L6 10 L14 18"/></svg>
  <div class="card" style="left:180px">
    <div class="stars">★★★★★</div>
    <h3>Great Pricing</h3>
    <p>Our carpets look brand new and the crew arrived right on time. Friendly, careful and fairly priced. We will book them again next season for sure.</p>
    <p class="author">By Author Name</p>
  </div>
  <div class="card" style="left:610px">
    <div class="stars">★★★★★</div>
    <h3>Great Pricing</h3>
    <p>They removed every pet stain from our area rug and the house smells fresh. Honest quote, no surprises and fast drying. Highly recommended to neighbors.</p>
    <p class="author">By Author Name</p>
  </div>
  <svg class="arrow" style="left:1040px;top:240px" viewBox="0 0 20 20"><path d="M6 2 L14 10 L6 18"/></svg>
</section>

<div class="badges">
  <div class="badge b-sq"></div>
  <div class="badge b-rect"></div>
  <div class="badge b-round"></div>
  <div class="badge b-round"></div>
  <div class="badge b-round"></div>
  <div class="badge b-sq"></div>
  <div class="badge b-round"></div>
</div>

<svg class="footer-wave" viewBox="0 0 1200 70" preserveAspectRatio="none">
  <path d="M0 20 Q600 80 1200 10 V70 H0Z" fill="#2e9d3a"/>
  <path d="M0 34 Q600 90 1200 24 V70 H0Z" fill="#0b2540"/>
</svg>
<footer class="footer">
  <div class="fcol" style="left:150px">
    <h3>QUICK LINKS</h3>
    <div class="links">
      <span>About Us</span><span>Service Areas</span>
      <span>Our Services</span><span>Testimonials</span>
      <span>Why Maple Rug</span><span>Sitemap</span>
      <span>Coupons</span><span>Blogs</span>
      <span>Gallery</span><span>Contact Us</span>
    </div>
  </div>
  <div class="fcol" style="left:520px">
    <h3>CONTACT US</h3>
    <p>2210 Alder Grove Rd<br>Maplewood, IL 60999<br>Get directions<br>(773) 555-0142<br>hello@maplerugvent.net</p>
  </div>
  <div class="fcol" style="left:820px">
    <h3>OPENING HOURS</h3>
    <p>Monday to Friday: 7 am to 6 pm<br>Saturday: 7 am to 3 pm<br>Sunday Closed</p>
    <div class="social"><i></i><i></i><i></i><i></i></div>
  </div>
  <div class="copy">© 2020 Company Name | All Rights Reserved | Disclaimer</div>
</footer>

</body>
</html>
```